KLV Plant Services

We are a heavy diesel mechanical business with additional air con certificates, remapping engine rebuilt

Contact Information for Business Card

Company Name, Director Name, Managing Director, Contact details, email and website

Font styles to use
Serif
Script

```html
<!DOCTYPE html>
<html lang="en">
<head>
<meta charset="UTF-8">
<title>KLV Plant Services – Business Card</title>
<link href="https://fonts.googleapis.com/css2?family=Arimo:wght@400;700&display=swap" rel="stylesheet">
<style>
  :root {
    --backdrop: #7f7f7f;
    --card-black: #000000;
    --card-white: #f4f4f6;
    --navy: #1a1f7a;
    --ink: #111111;
    --grey-text: #555555;
    --white: #ffffff;
    --edge: #1a1f7a;
  }
  * { margin: 0; padding: 0; box-sizing: border-box; }
  html, body {
    width: 1200px; height: 900px; overflow: hidden;
    background: var(--backdrop);
    font-family: "Arimo", Arial, sans-serif;
  }
  .stage {
    width: 1200px; height: 900px;
    display: flex; align-items: center; justify-content: center; gap: 40px;
  }
  .card {
    width: 560px; height: 320px;
    border-radius: 22px;
    position: relative; overflow: hidden;
    box-shadow: 0 8px 20px rgba(0,0,0,0.35);
  }
  /* Back side */
  .card-back {
    background: var(--card-black);
    display: flex; align-items: center; justify-content: center;
  }
  .brand {
    display: flex; align-items: center; gap: 14px;
  }
  .brand-dot {
    width: 34px; height: 34px; border-radius: 50%;
    background: currentColor;
  }
  .brand-name {
    font-weight: 700;
    white-space: nowrap;
  }
  .card-back .brand { color: var(--white); }
  .card-back .brand-name { font-size: 36px; }
  /* Front side */
  .card-front {
    background: var(--card-white);
    border-bottom: 3px solid var(--edge);
  }
  .hero-area {
    position: absolute; top: 0; right: 0;
    width: 210px; height: 100%;
    background: linear-gradient(160deg, #2a2a2a 0%, #000000 60%, #1c1c1c 100%);
    clip-path: polygon(18% 0, 100% 0, 100% 100%, 45% 100%, 25% 80%, 0 50%, 5% 10%);
  }
  .front-content {
    position: absolute; left: 30px; top: 30px;
  }
  .card-front .brand { color: var(--navy); gap: 8px; }
  .card-front .brand-dot { width: 18px; height: 18px; }
  .card-front .brand-name { font-size: 20px; }
  .person { margin-top: 26px; }
  .person-name { color: var(--navy); font-weight: 700; font-size: 22px; }
  .person-role { color: var(--grey-text); font-size: 14px; margin-top: 2px; }
  .address {
    margin-top: 22px; margin-left: 24px;
    color: var(--ink); font-size: 14px; line-height: 1.3;
  }
  .contacts {
    list-style: none; margin-top: 12px; margin-left: 24px;
    color: var(--ink); font-size: 14px; line-height: 1.35;
  }
  .contacts li { display: flex; align-items: center; gap: 8px; }
  .contacts svg { width: 12px; height: 12px; fill: var(--navy); flex: none; }
</style>
</head>
<body>
<main class="stage">
  <section class="card card-back">
    <div class="brand">
      <span class="brand-dot"></span>
      <span class="brand-name">KLV Plant Services</span>
    </div>
  </section>

  <section class="card card-front">
    <div class="hero-area" role="img" aria-label="Black silhouette of an excavator arm and bucket"></div>
    <div class="front-content">
      <div class="brand">
        <span class="brand-dot"></span>
        <span class="brand-name">KLV Plant Services</span>
      </div>
      <div class="person">
        <p class="person-name">Daniel Hart</p>
        <p class="person-role">Managing Director</p>
      </div>
      <p class="address">2170 Harbour Lane<br>Glen Cove, NY 11542</p>
      <ul class="contacts">
        <li>
          <svg viewBox="0 0 24 24"><path d="M6.6 10.8a15 15 0 0 0 6.6 6.6l2.2-2.2a1 1 0 0 1 1-.25 11.4 11.4 0 0 0 3.6.57 1 1 0 0 1 1 1V20a1 1 0 0 1-1 1A17 17 0 0 1 3 4a1 1 0 0 1 1-1h3.5a1 1 0 0 1 1 1c0 1.25.2 2.45.57 3.6a1 1 0 0 1-.25 1z"/></svg>
          (555) 0142-7781
        </li>
        <li>
          <svg viewBox="0 0 24 24"><path d="M2 5h20v14H2z M2 5l10 8 10-8" fill="none" stroke="#1a1f7a" stroke-width="2.5"/></svg>
          name@KLV.com
        </li>
        <li>
          <svg viewBox="0 0 24 24"><circle cx="12" cy="12" r="10"/></svg>
          www.KLV.com
        </li>
      </ul>
    </div>
  </section>
</main>
</body>
</html>
```